Webdesign für Bedrucken Papiertaschen, Schildern etc.
Zielgruppe
Wir bedrucken Papiertaschen, Papierbeutel, Laternen, Aluplaketten, Schilder, etc. und lasern Hundemarken. Zielgruppen von Privat bis Geschäftskunden
Aufgabenstellung
Der Shop sollte ein einfacher und kostengünstiger 'web2print'-shop werden. Wo die Kunden anhand von einem Editor Ihre Logos oder Druckvorlagen selber hochladen und/oder gestalten könne. Bisher haben die Kunden eifach ihre Bidldatei per E-Mail geschickt und wir haben diese dann weiter verarbeit.
Der Shop sollte, wenn möglich, günstig im Unterhalt sein, da wir nicht abschätzen können, wie gut diese laufen wird.
Wir haben wie 3 Bereich: 1. Papierbeutel/Taschen / 2. Stallplaketten (für z.B. Pferdesport) / 3. Diverses (Wie z.B. die Laternen, Schilder, Hundemarken, etc.)
Es würde sich um eine separate Webseite handeln. Daher ist bei Design freie Hand, eifach und klar... auch für nicht so ambitionierte Privatkunden oder kleine Unternehmen.

```html
<!DOCTYPE html>
<html lang="de">
<head>
<meta charset="utf-8">
<title>Beutelhaus – Web2Print</title>
<link href="https://fonts.googleapis.com/css2?family=Inter+Tight:wght@400;500;600;700;800&family=JetBrains+Mono:wght@400;500&display=swap" rel="stylesheet">
<style>
:root{
  --red:#e02a1d;
  --ink:#141414;
  --text:#2b2b2b;
  --muted:#6b6b6b;
  --line:#e3e3e3;
  --soft:#f6f6f6;
  --white:#ffffff;
  --black:#000000;
}
*{box-sizing:border-box;margin:0;padding:0}
html,body{width:1200px;height:2859px;overflow:hidden}
body{font-family:"Inter Tight",Arial,sans-serif;color:var(--text);background:var(--white);position:relative}
.mono{font-family:"JetBrains Mono",monospace}
a{color:inherit;text-decoration:none}

/* top bar */
.topbar{height:24px;background:var(--black);color:#fff;display:flex;justify-content:space-between;align-items:center;padding:0 47px;font-size:9.5px;letter-spacing:.06em}
.topbar .dot{display:inline-block;width:5px;height:5px;border-radius:50%;background:var(--red);margin-right:6px;vertical-align:1px}

/* header */
.header{height:68px;display:flex;align-items:center;padding:0 47px;border-bottom:1px solid var(--line);background:#fff}
.logo{font-weight:800;font-size:17px;letter-spacing:-.03em;color:var(--ink);width:150px;display:flex;align-items:center;gap:6px}
.logo .sq{width:12px;height:12px;background:var(--ink)}
.nav{display:flex;gap:24px;font-size:13px;font-weight:500;color:var(--ink);margin-left:54px}
.header-tools{margin-left:auto;display:flex;gap:14px;align-items:center}
.icon-btn{width:30px;height:30px;border:1px solid var(--line);border-radius:50%;display:flex;align-items:center;justify-content:center}
.cart{background:var(--red);color:#fff;border-radius:20px;height:32px;padding:0 10px 0 14px;display:flex;align-items:center;gap:8px;font-size:12.5px;font-weight:600}
.cart .count{background:#fff;color:var(--red);width:17px;height:17px;border-radius:50%;font-size:9px;display:flex;align-items:center;justify-content:center}

/* hero */
.hero{position:relative;height:653px;background:#fff;overflow:hidden;border-bottom:1px solid var(--line)}
.hero-photo{position:absolute;right:0;top:0;width:645px;height:100%;background:linear-gradient(90deg,rgba(255,255,255,1) 0%,rgba(236,233,228,.7) 25%,#d9cbb8 55%,#c8a987 80%,#e8d8c6 100%)}
.hero-copy{position:absolute;left:47px;top:172px}
.hero h1{font-size:67px;line-height:68px;font-weight:700;letter-spacing:-.045em;color:var(--ink)}
.hero h1 .accent{color:var(--red)}
.hero p{margin-top:24px;width:430px;font-size:14px;line-height:21px;color:var(--text)}
.btn-row{display:flex;gap:12px;margin-top:24px}
.btn{height:48px;border-radius:24px;display:inline-flex;align-items:center;gap:8px;padding:0 24px;font-size:13.5px;font-weight:600}
.btn-red{background:var(--red);color:#fff}
.btn-line{border:1.5px solid var(--ink);color:var(--ink);background:#fff}
.stats{display:flex;gap:30px;margin-top:30px}
.stat b{display:block;font-size:26px;font-weight:600;letter-spacing:-.03em;color:var(--ink);line-height:28px}
.stat span{font-size:9.5px;letter-spacing:.08em;color:var(--muted)}

/* section shared */
.soft{background:var(--soft)}
.eyebrow{font-size:9.5px;letter-spacing:.08em;color:var(--muted)}
.h2{font-size:44px;line-height:45px;font-weight:700;letter-spacing:-.035em;color:var(--ink)}

.process{position:relative;height:1256px;padding:41px 47px 0}
.process .h2{margin-top:12px}
.pill-red{position:absolute;right:47px;top:103px;height:40px;border-radius:20px;background:var(--red);color:#fff;font-size:13px;font-weight:600;display:flex;align-items:center;gap:10px;padding:0 20px}
.steps{position:relative;margin-top:50px;height:190px}
.track{position:absolute;left:30px;right:10px;top:29px;height:1px;background:var(--line)}
.track-red{position:absolute;left:30px;width:255px;top:29px;height:1.5px;background:var(--red);opacity:.6}
.target{position:absolute;right:0;top:22px}
.step{position:absolute;top:0;width:250px}
.circle{width:58px;height:58px;border-radius:50%;border:1px solid #cfcfcf;background:#fff;display:flex;align-items:center;justify-content:center;position:relative}
.circle span{width:46px;height:46px;border-radius:50%;border:1px solid #d6d6d6;display:flex;align-items:center;justify-content:center;font-weight:600;font-size:16px;color:var(--ink)}
.circle.on{border:2px solid var(--red)}
.circle.on span{background:var(--red);border-color:var(--red);color:#fff}
.tag{display:inline-block;margin-top:16px;border:1px solid var(--line);border-radius:10px;padding:1px 7px;font-size:8.5px;color:var(--muted);background:#fff;letter-spacing:.05em}
.step h3{font-size:18px;font-weight:600;letter-spacing:-.02em;color:var(--ink);margin-top:14px}
.step p{font-size:11.5px;line-height:17px;margin-top:6px;width:215px}

.range{margin-top:36px}
.range .h2{margin-top:14px}
.all-link{position:absolute;right:47px;top:506px;font-size:12.5px;font-weight:600;color:var(--ink)}
.cards{display:flex;gap:20px;margin-top:24px}
.card{width:355px;height:316px;background:#fff;border:1px solid var(--line);border-radius:10px;overflow:hidden}
.card .img{height:166px}
.card .body{padding:20px 20px 0}
.card h3{font-size:20px;font-weight:600;letter-spacing:-.025em;color:var(--ink)}
.card p{font-size:12px;line-height:19px;margin-top:8px;height:38px}
.card .foot{display:flex;justify-content:space-between;align-items:center;margin-top:18px}
.card .foot .tag{margin:0}
.card .foot a{font-size:12.5px;font-weight:600;color:var(--ink)}

.b2b{position:relative;margin-top:38px;height:300px;background:#fff;border:1px solid var(--line);border-radius:14px;padding:38px 41px}
.b2b .h2{font-size:38px;line-height:37px;margin-top:12px}
.b2b p{font-size:12.5px;line-height:19px;width:390px;margin-top:16px}
.b2b .btn-row{margin-top:20px}
.b2b .btn{height:40px;padding:0 19px;font-size:12.5px}
.prices{position:absolute;right:40px;top:81px;display:grid;grid-template-columns:repeat(3,144px);gap:10px 10px}
.price{height:64px;border:1px solid var(--line);border-radius:6px;padding:14px 14px 0;background:#fff}
.price small{display:block;font-size:9px;letter-spacing:.08em;color:var(--muted)}
.price b{display:block;font-size:19px;font-weight:700;letter-spacing:-.02em;color:var(--ink);margin-top:3px}
.price.hot{background:var(--red);border-color:var(--red)}
.price.hot small,.price.hot b{color:#fff}

/* features */
.features{height:289px;display:flex;border-bottom:1px solid var(--line);padding:58px 47px 0;background:#fff}
.feature{flex:1;text-align:center;border-right:1px solid var(--line);height:168px}
.feature:last-child{border-right:0}
.feature .ico{width:60px;height:60px;border-radius:50%;background:var(--red);margin:14px auto 0;display:flex;align-items:center;justify-content:center}
.feature h4{font-size:16px;font-weight:600;color:var(--ink);margin-top:22px}
.feature p{font-size:11.5px;line-height:17px;color:var(--muted);margin:13px auto 0;width:170px}

/* reviews */
.reviews{height:268px;display:flex;gap:18px;padding:45px 47px 0;background:#fff}
.review{flex:1;height:157px;border:1px solid var(--line);border-radius:10px;padding:20px 22px}
.stars{color:var(--red);font-size:11px;letter-spacing:3px}
.review q{display:block;font-size:16.5px;line-height:22px;color:var(--ink);margin-top:10px;quotes:none}
.review .who{font-size:9px;letter-spacing:.08em;color:var(--muted);position:relative;margin-top:16px}

/* footer */
.footer{position:absolute;left:0;right:0;top:2558px;height:301px;background:var(--black);color:#fff;padding:40px 47px 0}
.footer .logo{color:#fff}
.footer .logo .sq{background:#fff}
.foot-grid{display:flex}
.foot-about{width:434px}
.foot-about p{font-size:11.5px;line-height:17px;margin-top:20px;width:260px;color:#e8e8e8}
.foot-col{width:238px}
.foot-col h5{font-size:11.5px;font-weight:700;letter-spacing:.06em;margin-top:7px}
.foot-col ul{list-style:none;margin-top:14px}
.foot-col li{font-size:11.5px;line-height:21.7px;color:#e8e8e8}
.foot-bottom{position:absolute;left:47px;right:47px;bottom:14px;border-top:1px solid #2a2a2a;padding-top:16px;display:flex;justify-content:space-between;font-size:9.5px;letter-spacing:.04em}
.foot-bottom .pay{display:flex;gap:16px}
</style>
</head>
<body>

<div class="topbar mono">
  <span><span class="dot"></span>VERSAND CH AB CHF 9.50 — DE/FR/IT VERFÜGBAR</span>
  <span>DRUCK IN 3–5 WERKTAGEN · LASERGRAVUR AB 24 H</span>
  <span>HILFE? +41 44 000 12 34</span>
</div>

<header class="header">
  <div class="logo"><span class="sq"></span>Beutelhaus</div>
  <nav class="nav">
    <a>Papierbeutel &amp; Taschen</a><a>Stallplaketten</a><a>Hundemarken &amp; Diverses</a><a>Über uns</a><a>Hilfe</a>
  </nav>
  <div class="header-tools">
    <span class="icon-btn"><svg width="12" height="12" viewBox="0 0 12 12" fill="none" stroke="#141414" stroke-width="1.3"><circle cx="5" cy="5" r="3.6"/><path d="M8 8l3 3"/></svg></span>
    <span class="icon-btn"><svg width="12" height="12" viewBox="0 0 12 12" fill="none" stroke="#141414" stroke-width="1.2"><circle cx="6" cy="4" r="2.3"/><path d="M1.8 11c.6-2.4 2.2-3.4 4.2-3.4s3.6 1 4.2 3.4"/></svg></span>
    <span class="cart"><svg width="12" height="12" viewBox="0 0 12 12" fill="none" stroke="#fff" stroke-width="1.2"><path d="M1 1.5h2l1.2 6h5.6l1-4.5H3.5"/><circle cx="5" cy="10" r=".8"/><circle cx="9" cy="10" r=".8"/></svg>Warenkorb <span class="count mono">0</span></span>
  </div>
</header>

<section class="hero">
  <div class="hero-photo" role="img" aria-label="Foto: Person trägt eine Papiertüte mit frischem Gemüse und telefoniert"></div>
  <div class="hero-copy">
    <h1>Ihr Design.<br><span class="accent">Digital</span> bestellt.<br>Präzise produziert.</h1>
    <p>Papierbeutel, Stallplaketten, Hundemarken und mehr — gestalten Sie Ihr Produkt direkt im Browser. Vorlage hochladen, Vorschau prüfen, drucken lassen. Ohne E-Mail-Ping-Pong, ohne Wartezeit.</p>
    <div class="btn-row">
      <a class="btn btn-red"><svg width="13" height="13" viewBox="0 0 13 13" fill="none" stroke="#fff" stroke-width="1.3"><path d="M2 11l.6-2.6L9 2l2 2-6.4 6.4z"/></svg>Jetzt gestalten</a>
      <a class="btn btn-line">Materialmuster bestellen <svg width="12" height="10" viewBox="0 0 12 10" fill="none" stroke="#141414" stroke-width="1.3"><path d="M1 5h9M6.5 1.5L10 5l-3.5 3.5"/></svg></a>
    </div>
    <div class="stats">
      <div class="stat"><b>3–5</b><span class="mono">TAGE DRUCK</span></div>
      <div class="stat"><b>ab 1</b><span class="mono">STÜCK HUNDEMARKEN</span></div>
      <div class="stat"><b>100%</b><span class="mono">FSC-PAPIER</span></div>
      <div class="stat"><b>CH</b><span class="mono">PRODUKTION</span></div>
    </div>
  </div>
</section>

<section class="process soft">
  <div class="eyebrow mono">ABLAUF</div>
  <h2 class="h2">In vier Schritten<br>zum gedruckten Produkt.</h2>
  <a class="pill-red">Produkt wählen <svg width="11" height="9" viewBox="0 0 12 10" fill="none" stroke="#fff" stroke-width="1.4"><path d="M1 5h9M6.5 1.5L10 5l-3.5 3.5"/></svg></a>

  <div class="steps">
    <div class="track"></div><div class="track-red"></div>
    <svg class="target" width="14" height="14" viewBox="0 0 14 14" fill="none" stroke="#e02a1d" stroke-width="1.3"><circle cx="7" cy="7" r="4"/><path d="M7 0v4M7 10v4M0 7h4M10 7h4"/></svg>
    <div class="step" style="left:0"><div class="circle on"><span>01</span></div><span class="tag mono">~ 2 MIN.</span><h3>Produkt wählen</h3><p>Format, Material, Auflage. Live-Preisb erechnung.</p></div>
    <div class="step" style="left:282px"><div class="circle"><span>02</span></div><span class="tag mono">5–15 MIN.</span><h3>Im Editor gestalten</h3><p>Logo hochladen, Text setzen — oder Druckdatei anliefern.</p></div>
    <div class="step" style="left:564px"><div class="circle"><span>03</span></div><span class="tag mono">~ 1 MIN.</span><h3>Bestellung freigeben</h3><p>Vorschau prüfen, bezahlen per Tapflow, Karte oder Rechnung.</p></div>
    <div class="step" style="left:846px"><div class="circle"><span>04</span></div><span class="tag mono">3–5 TAGE</span><h3>Drucken &amp; liefern</h3><p>Produktion in der Schweiz, Versand in 3–5 Werktagen.</p></div>
  </div>

  <div class="range">
    <div class="eyebrow mono">SORTIMENT</div>
    <h2 class="h2">Drei Produktwelten.<br>Ein Workflow.</h2>
  </div>
  <a class="all-link" style="top:1251px">Alle Produkte ansehen &nbsp;→</a>

  <div class="cards">
    <article class="card">
      <div class="img" role="img" aria-label="Foto: bedruckte Papiertragetasche in der Hand" style="background:linear-gradient(120deg,#3b4660 0%,#8b7a66 45%,#d7b892 70%,#b9a38a 100%)"></div>
      <div class="body"><h3>Papierbeutel &amp; Taschen</h3><p>Vom Brötchenbeutel bis zur Tragetasche mit Henkel. 1-farbig bis Vollfarbe.</p>
      <div class="foot"><span class="tag mono">AB 100 STK.</span><a>Entdecken &nbsp;→</a></div></div>
    </article>
    <article class="card">
      <div class="img" role="img" aria-label="Foto: Stallgasse mit hölzernen Pferdeboxen" style="background:linear-gradient(180deg,#6f5a45 0%,#8a5a34 45%,#5a3a22 80%,#7a6350 100%)"></div>
      <div class="body"><h3>Stallplaketten</h3><p>Pferdesport, Boxschilder, Boxenbeschriftung. Aluminium oder Kunststoff.</p>
      <div class="foot"><span class="tag mono">AB 1 STK.</span><a>Entdecken &nbsp;→</a></div></div>
    </article>
    <article class="card">
      <div class="img" role="img" aria-label="Foto: Hund mit Hundemarke liegt im Gras" style="background:linear-gradient(180deg,#6f8a3a 0%,#a06a3a 45%,#5f7d2c 100%)"></div>
      <div class="body"><h3>Hundemarken &amp; Diverses</h3><p>Lasergravur auf Alu/Edelstahl. Plus Laternen, Schilder und Werbeartikel.</p>
      <div class="foot"><span class="tag mono">AB 1 STK.</span><a>Entdecken &nbsp;→</a></div></div>
    </article>
  </div>

  <div class="b2b">
    <div class="eyebrow mono">GESCHÄFTSKUNDEN</div>
    <h2 class="h2">Grossauflagen?<br>Wir offerieren in 24 Std.</h2>
    <p>Ab 5'000 Beuteln wechseln wir vom Digital- in den Flexodruck. Bis zu 50 % günstiger. Senden Sie uns Format, Auflage und Druckdaten — wir melden uns am nächsten Werktag.</p>
    <div class="btn-row">
      <a class="btn btn-red">Offerte anfordern</a>
      <a class="btn btn-line">Mengenrabatt-Tabelle &nbsp;→</a>
    </div>
    <div class="prices">
      <div class="price"><small class="mono">500 STK.</small><b>CHF 0.42</b></div>
      <div class="price"><small class="mono">1'000 STK.</small><b>CHF 0.31</b></div>
      <div class="price"><small class="mono">2'500 STK.</small><b>CHF 0.24</b></div>
      <div class="price hot"><small class="mono">5'000 STK.</small><b>CHF 0.18</b></div>
      <div class="price"><small class="mono">10'000 STK.</small><b>CHF 0.14</b></div>
      <div class="price"><small class="mono">25'000 STK.</small><b>Offerte</b></div>
    </div>
  </div>
</section>

<section class="features">
  <div class="feature"><div class="ico"><svg width="22" height="22" viewBox="0 0 22 22" fill="none" stroke="#fff" stroke-width="1.6"><path d="M2 6h11v9H2zM13 9h4l3 3v3h-7"/><circle cx="6" cy="16.5" r="1.8"/><circle cx="16" cy="16.5" r="1.8"/></svg></div><h4>Schweizer Produktion</h4><p>Druck und Versand aus 8000 Zürich.</p></div>
  <div class="feature"><div class="ico"><svg width="22" height="22" viewBox="0 0 22 22" fill="none" stroke="#fff" stroke-width="1.6"><path d="M11 2l7 3v5c0 5-3 8-7 10-4-2-7-5-7-10V5z"/><path d="M8 11l2 2 4-4"/></svg></div><h4>Druckvorschau garantiert</h4><p>Was Sie im Editor sehen, kommt so an.</p></div>
  <div class="feature"><div class="ico"><svg width="22" height="22" viewBox="0 0 22 22" fill="none" stroke="#fff" stroke-width="1.6"><path d="M5 18C5 9 10 4 18 4c0 8-5 13-13 14zM5 18l6-6"/></svg></div><h4>Nachhaltigkeit</h4><p>Nachhaltige Materialien als Standard.</p></div>
  <div class="feature"><div class="ico"><svg width="22" height="22" viewBox="0 0 22 22" fill="none" stroke="#fff" stroke-width="1.6"><path d="M12 2L4 13h6l-1 7 8-11h-6z"/></svg></div><h4>Express ab 24 h</h4><p>Hundemarken und Stallplaketten schnell.</p></div>
</section>

<section class="reviews">
  <div class="review"><div class="stars">☆☆☆☆☆</div><q>„Endlich kein Datei-Pingpong mehr. Hundemarke samt Gravur in zwei Tagen geliefert."</q><div class="who mono">LENA M. · HUNDETRAINERIN, BERN</div></div>
  <div class="review"><div class="stars">☆☆☆☆☆</div><q>„Wir bestellen 2× jährlich 8'000 Bäckerbeutel. Preise stimmen, Termine stimmen."</q><div class="who mono">BÄCKEREI KORN &amp; KRUSTE, LUZERN</div></div>
  <div class="review"><div class="stars">☆☆☆☆☆</div><q>„Stallplaketten für 22 Boxen — Editor war erstaunlich klar. Auch für Nicht-Designer."</q><div class="who mono" style="margin-top:38px">REITSTALL TANNHOF</div></div>
</section>

<footer class="footer">
  <div class="foot-grid">
    <div class="foot-about">
      <div class="logo"><span class="sq"></span>Beutelhaus</div>
      <p>Druckerei und Lasergravur aus der Schweiz. Wir bedrucken Papierbeutel, Stallplaketten, Laternen, Schilder und lasern Hundemarken — vom Einzelstück bis zur Grossauflage.</p>
    </div>
    <div class="foot-col"><h5>PRODUKTE</h5><ul><li>Papierbeutel</li><li>Papiertaschen</li><li>Stallplaketten</li><li>Hundemarken</li><li>Laternen &amp; Schilder</li><li>Aluplaketten</li></ul></div>
    <div class="foot-col"><h5>SERVICE</h5><ul><li>Druckvorlagen-Editor</li><li>Druckdaten anliefern</li><li>Materialmuster bestellen</li><li>Mengenrabatte</li><li>Versand &amp; Lieferung</li><li>Hilfe &amp; FAQ</li></ul></div>
    <div class="foot-col"><h5>FIRMA</h5><ul><li>Über uns</li><li>Nachhaltigkeit</li><li>Geschäftskunden</li><li>Kontakt</li><li>AGB</li><li>Impressum</li></ul></div>
  </div>
  <div class="foot-bottom mono">
    <span>© 2026 Beutelhaus · Kessler Kunststoff AG · CH-8999 Mattwil / Zürich</span>
    <span class="pay"><span>Tapflow</span><span>Cardia</span><span>Mondcard</span><span>Rechnung</span><span>Postgiro</span></span>
  </div>
</footer>

</body>
</html>
```